Corporate Design für logopädische Praxis
Zielgruppe
Ich gründe eine logopädische Praxis, die Sprachtherapie sowohl für Erwachsene als auch Kinder anbietet und damit ein Logo benötigt, das jede Altersgruppe anspricht und 'Lindenhof' als fachliche und menschliche Qualitätszeit interpretiert.
Aufgabenstellung
Ich bevorzuge ein klares Design, welches das Wortspiel der 'Lindenhof' im Idealfall aufgreift und den Patienten vermittelt, dass sowohl die fachliche Qualität der Behandlung als auch die Ebene von Empathie und Patientenorientierung im zwischenmenschlichen Umgang für die Praxis zentral sind.

```html
<!DOCTYPE html>
<html lang="de">
<head>
<meta charset="utf-8">
<title>Lindenhof – Praxis für Logopädie</title>
<link href="https://fonts.googleapis.com/css2?family=Montserrat:wght@300;400&family=Roboto:wght@300;400&display=swap" rel="stylesheet">
<style>
:root{
  --mauve:#a692ab;
  --mauve-dark:#8c7d90;
  --paper:#ffffff;
  --canvas-light:#fdfdfd;
  --canvas-dark:#3d3d3d;
  --ink:#333333;
  --ink-soft:#7b7b7b;
  --wave:#f2f1f5;
  --rule:#cfcfd4;
}
*{margin:0;padding:0;box-sizing:border-box}
html,body{width:1200px;height:2760px;overflow:hidden}
body{position:relative;background:var(--canvas-light);font-family:'Montserrat',sans-serif;color:var(--ink)}
.stage-dark{position:absolute;left:0;top:978px;width:1200px;height:1782px;background:var(--canvas-dark)}

/* brand lockup */
.brand{position:absolute;display:flex;align-items:center;white-space:nowrap}
.brand-dot{border-radius:50%;background:var(--mauve);flex:none}
.brand-text{display:flex;flex-direction:column}
.brand-name{font-family:'Montserrat',sans-serif;font-weight:300;color:var(--mauve);line-height:1}
.brand-tag{font-family:'Montserrat',sans-serif;font-weight:300;color:var(--mauve-dark);line-height:1;text-align:right}

.brand--hero{left:290px;top:418px}
.brand--hero .brand-dot{width:150px;height:150px;margin-right:20px}
.brand--hero .brand-name{font-size:84px;letter-spacing:2px}
.brand--hero .brand-tag{font-size:26px;letter-spacing:3px;margin-top:12px}

.card{position:absolute;top:1035px;width:381px;height:246px;background:var(--paper);overflow:hidden}
.card--front{left:191px}
.card--back{left:629px}
.brand--card .brand-dot{width:60px;height:60px;margin-right:9px}
.brand--card .brand-name{font-size:36px;letter-spacing:1px}
.brand--card .brand-tag{font-size:12px;letter-spacing:2px;margin-top:5px}
.card--front .brand{left:58px;top:92px}
.card--back .brand{left:34px;top:38px}

.card-person{position:absolute;left:34px;top:152px;font-size:10px;line-height:15px;color:var(--ink-soft)}
.card-person .name{color:var(--ink);letter-spacing:.5px;font-size:11px}
.card-person .addr{margin-top:16px}
.card-contacts{position:absolute;left:208px;top:150px;list-style:none;font-size:9.5px;color:var(--ink-soft)}
.card-contacts li{display:flex;align-items:center;height:16px}

.icon{display:inline-block;width:11px;height:11px;border-radius:50%;background:var(--mauve);margin-right:7px;flex:none}
.icon--lg{width:17px;height:17px;margin-right:9px}

/* letter */
.letter{position:absolute;left:131px;top:1328px;width:939px;height:1328px;background:var(--paper);overflow:hidden;font-family:'Roboto',sans-serif}
.letter .brand{right:74px;top:82px}
.brand--letter .brand-dot{width:90px;height:90px;margin-right:12px}
.brand--letter .brand-name{font-size:52px;letter-spacing:1px}
.brand--letter .brand-tag{font-size:17px;letter-spacing:3px;margin-top:6px}

.fold-mark{position:absolute;left:0;width:23px;height:1px;background:#777}
.sender-line{position:absolute;left:117px;top:262px;font-size:9px;color:var(--ink-soft)}
.recipient{position:absolute;left:117px;top:284px;font-size:16px;line-height:19px;font-weight:300;color:#222}
.letter-body{position:absolute;left:117px;top:465px;width:712px;font-size:15.6px;line-height:19px;font-weight:300;color:#222}
.letter-body p{margin-bottom:19px}
.letter-body .salutation{margin-bottom:38px}
.closing{position:absolute;left:117px;top:947px;font-size:15.6px;font-weight:300;color:#222}
.signature{position:absolute;left:117px;top:990px;width:150px;height:80px;background:linear-gradient(135deg,#eef0f6,#f7f7fa)}

.wave{position:absolute;left:0;top:940px;width:939px;height:388px}
.letter-footer{position:absolute;left:117px;top:1188px;display:flex;font-size:11px;color:var(--ink-soft)}
.footer-col{list-style:none;padding:0 24px;border-left:1px solid var(--rule);height:90px}
.footer-col:first-child{padding-left:0;border-left:none}
.footer-col li{height:24px;display:flex;align-items:center;white-space:nowrap}
</style>
</head>
<body>

<div class="brand brand--hero">
  <span class="brand-dot"></span>
  <div class="brand-text"><span class="brand-name">Lindenhof</span><span class="brand-tag">Praxis für Logopädie</span></div>
</div>

<div class="stage-dark"></div>

<section class="card card--front">
  <div class="brand brand--card">
    <span class="brand-dot"></span>
    <div class="brand-text"><span class="brand-name">Lindenhof</span><span class="brand-tag">Praxis für Logopädie</span></div>
  </div>
</section>

<section class="card card--back">
  <div class="brand brand--card">
    <span class="brand-dot"></span>
    <div class="brand-text"><span class="brand-name">Lindenhof</span><span class="brand-tag">Praxis für Logopädie</span></div>
  </div>
  <div class="card-person">
    <div class="name">MAX MUSTERMANN</div>
    <div>Geschäftsführer</div>
    <div class="addr">Musterweg 13<br>54321 Musterdorf</div>
  </div>
  <ul class="card-contacts">
    <li><span class="icon"></span>+49 (0)1234 5 67 89-0</li>
    <li><span class="icon"></span>+49 (0)1234 5 67 89-50</li>
    <li><span class="icon"></span>+49 (0)123 4 56 78 90</li>
    <li><span class="icon"></span>info@yourcompany.de</li>
    <li><span class="icon"></span>yourcompany.de</li>
  </ul>
</section>

<article class="letter">
  <div class="brand brand--letter">
    <span class="brand-dot"></span>
    <div class="brand-text"><span class="brand-name">Lindenhof</span><span class="brand-tag">Praxis für Logopädie</span></div>
  </div>

  <span class="fold-mark" style="top:468px"></span>
  <span class="fold-mark" style="top:929px"></span>

  <div class="sender-line">Your Company | Musterweg 13 | 54321 Musterdorf</div>
  <div class="recipient">Max Mustermann<br>Musterstr. 1<br>12345 Muster</div>

  <div class="letter-body">
    <p class="salutation">Sehr geehrte Damen und Herren,</p>
    <p>Lorem ipsum dolor sit amet, consetetur sadipscing elitr, sed diam nonumy eirmod tempor invidunt ut labore et dolore magna aliquyam erat, sed diam voluptua. At vero eos et accusam et justo duo dolores et ea rebum. Stet clita kasd gubergren, no sea takimata sanctus est Lorem ipsum dolor sit amet. Lorem ipsum dolor sit amet, consetetur sadipscing elitr, sed diam nonumy eirmod tempor invidunt ut labore et dolore magna aliquyam erat, sed diam voluptua. At vero eos et accusam et justo duo dolores et ea rebum. Stet clita kasd gubergren, no sea takimata sanctus est Lorem ipsum dolor sit amet. Lorem ipsum dolor sit amet, consetetur sadipscing elitr, sed diam nonumy eirmod tempor invidunt ut labore et dolore magna aliquyam erat, sed diam voluptua. At vero eos et accusam et justo duo dolores et ea rebum. Stet clita kasd gubergren, no sea takimata sanctus est Lorem ipsum dolor sit amet.</p>
    <p>Duis autem vel eum iriure dolor in hendrerit in vulputate velit esse molestie consequat, vel illum dolore eu feugiat nulla facilisis at vero eros et accumsan et iusto odio dignissim qui blandit praesent luptatum zzril delenit augue duis dolore te feugait nulla facilisi. Lorem ipsum dolor sit amet, consectetuer adipiscing elit, sed diam nonummy nibh euismod tincidunt ut laoreet dolore magna aliquam erat volutpat.</p>
    <p>Ut wisi enim ad minim veniam, quis nostrud exerci tation ullamcorper suscipit lobortis nisl ut aliquip ex ea commodo consequat. Duis autem vel eum iriure dolor in hendrerit in vulputate velit esse molestie consequat, vel illum dolore eu feugiat nulla facilisis at vero eros et accumsan et iusto odio dignissim qui blandit praesent luptatum zzril delenit augue duis dolore te feugait nulla facilisi.</p>
  </div>

  <svg class="wave" viewBox="0 0 939 388" preserveAspectRatio="none" aria-hidden="true">
    <path d="M0 190 C 260 180, 420 150, 600 80 C 760 20, 880 10, 939 5 L939 388 L0 388 Z" fill="var(--wave)"/>
  </svg>

  <div class="closing">Mit freundlichen Grüßen</div>
  <div class="signature" role="img" aria-label="Handschriftliche Unterschrift"></div>

  <div class="letter-footer">
    <ul class="footer-col">
      <li><span class="icon icon--lg"></span>+49 (0)1234 5 67 89-0</li>
      <li><span class="icon icon--lg"></span>+49 (0)1234 5 67 89-50</li>
      <li><span class="icon icon--lg"></span>info@yourcompany.de</li>
      <li><span class="icon icon--lg"></span>yourcompany.de</li>
    </ul>
    <ul class="footer-col">
      <li>MAX MUSTERMANN</li><li>Geschäftsführer</li><li>Musterweg 13</li><li>54321 Musterdorf</li>
    </ul>
    <ul class="footer-col">
      <li>Regionalbank Mitte</li><li>IBAN: DE43 XXXX 0110 XXXX 0481 XX</li><li>BIC: KRXXDE55XXX</li><li>Geschäftsführer: Max Mustermann</li>
    </ul>
    <ul class="footer-col">
      <li>Ust. ID: DE2XX9XX10X</li><li>HRB 1XX4XX</li><li>Amtsgericht Saarbrücken</li><li>Gesellschaftssitz: Schwalbach</li>
    </ul>
  </div>
</article>

</body>
</html>
```